Irrigation Business needs their business cards modernised and revamped

I would like to keep my current logo, colours and revamp the format of the card.

I would like the card to be clean yet important.

Im not sure if you include texture but i would like the named logo to be indented into the card etc.

show me something alive and free something thats clinical to the point yet has a feel of achievement. i would like people to go nice card.

Target Market(s)

high end clients, corporate, sports field manger, the guys that make the decisions

Industry/Entity Type

Business

Contact Information for Business Card

nformation to be included

Dean Harlow (Director)
0487305526
dean@kolvat.biz
www.kestonfieldworks.com

instagram logo
google logo
facebook logo

Colors

Designer to choose colors to be used in the design.

Requirements
Nice to have
• indentations a really nice feel to the card good texture

```html
<!DOCTYPE html>
<html lang="en">
<head>
<meta charset="utf-8">
<title>Keston Fieldworks – Business Card</title>
<link rel="stylesheet" href="https://fonts.googleapis.com/css2?family=Roboto:wght@400;500;700&family=Roboto+Condensed:wght@700&display=swap">
<style>
  :root {
    --backdrop: #2b2b2b;
    --card-white: #f2f2f2;
    --sky-blue: #2ea0d0;
    --deep-blue: #2f63a8;
    --logo-blue: #2f63a8;
    --field-green: #289c58;
    --white: #ffffff;
  }
  * { margin: 0; padding: 0; box-sizing: border-box; }
  html, body {
    width: 1200px; height: 960px; overflow: hidden;
    background: var(--backdrop);
    font-family: "Roboto", Arial, sans-serif;
  }
  .canvas { position: relative; width: 1200px; height: 960px; }
  .card {
    position: absolute; width: 600px; height: 342px; overflow: hidden;
    box-shadow: 0 2px 6px rgba(0,0,0,.45);
  }
  .card-front { left: 314px; top: 113px; background: var(--card-white); }
  .card-back { left: 311px; top: 472px; background: var(--field-green); }

  .front-art { position: absolute; inset: 0; }

  .brand {
    position: absolute; display: flex; flex-direction: column; align-items: center;
    font-weight: 700; letter-spacing: .5px; white-space: nowrap;
  }
  .brand-dot { border-radius: 50%; }
  .card-front .brand { left: 313px; width: 260px; top: 45px; color: var(--logo-blue); font-size: 23px; }
  .card-front .brand-dot { width: 80px; height: 80px; background: var(--logo-blue); margin-bottom: 17px; }
  .card-back .brand { left: 0; width: 600px; top: 80px; color: var(--white); font-size: 31px; }
  .card-back .brand-dot { width: 106px; height: 106px; background: var(--white); margin-bottom: 15px; }

  .contact-block { position: absolute; left: 32px; top: 206px; color: var(--white); }
  .person-name {
    font-family: "Roboto Condensed", Arial, sans-serif; font-weight: 700;
    font-size: 21px; letter-spacing: .3px; line-height: 26px;
  }
  .person-role { font-size: 14px; font-weight: 500; letter-spacing: .5px; margin-top: 2px; }
  .contact-list { list-style: none; margin-top: 14px; font-size: 14px; }
  .contact-list li { display: flex; align-items: center; height: 19px; }
  .contact-list svg { width: 13px; height: 13px; margin-right: 9px; fill: var(--white); }

  .social-row { position: absolute; left: 0; top: 290px; width: 600px; height: 28px; }
  .social-rule { position: absolute; top: 13px; height: 1px; width: 185px; }
  .social-rule.left { left: 70px; background: linear-gradient(90deg, rgba(255,255,255,0), rgba(255,255,255,.6)); }
  .social-rule.right { left: 355px; background: linear-gradient(90deg, rgba(255,255,255,.6), rgba(255,255,255,0)); }
  .social-links { position: absolute; left: 259px; top: 0; display: flex; gap: 3px; }
  .social-link { width: 28px; height: 28px; border-radius: 50%; background: var(--white); }
</style>
</head>
<body>
<main class="canvas">

  <section class="card card-front" aria-label="Business card front">
    <svg class="front-art" width="600" height="342" viewBox="0 0 600 342" aria-hidden="true">
      <polygon points="0,188 242,188 360,342 0,342" fill="var(--sky-blue)"/>
      <polygon points="304,263 600,263 600,342 365,342" fill="var(--deep-blue)"/>
      <g stroke="var(--card-white)" stroke-width="3">
        <line x1="300" y1="281.5" x2="600" y2="281.5"/>
        <line x1="300" y1="301.5" x2="600" y2="301.5"/>
        <line x1="300" y1="322.5" x2="600" y2="322.5"/>
      </g>
      <line x1="247" y1="188" x2="366" y2="342" stroke="var(--card-white)" stroke-width="4"/>
    </svg>

    <div class="brand">
      <span class="brand-dot" aria-hidden="true"></span>
      <span class="brand-name">KESTON FIELDWORKS</span>
    </div>

    <div class="contact-block">
      <p class="person-name">DEAN HARLOW</p>
      <p class="person-role">DIRECTOR</p>
      <ul class="contact-list">
        <li>
          <svg viewBox="0 0 24 24" aria-hidden="true"><path d="M6.6 10.8a15.1 15.1 0 0 0 6.6 6.6l2.2-2.2c.3-.3.7-.4 1-.2 1.1.4 2.3.6 3.6.6.6 0 1 .4 1 1V20c0 .6-.4 1-1 1A17 17 0 0 1 3 4c0-.6.4-1 1-1h3.5c.6 0 1 .4 1 1 0 1.3.2 2.5.6 3.6.1.3 0 .7-.2 1z"/></svg>
          0487305526
        </li>
        <li>
          <svg viewBox="0 0 24 24" aria-hidden="true"><path d="M2 5h20v14H2zm2 2v.5l8 5 8-5V7l-8 5z"/></svg>
          dean@kolvat.biz
        </li>
        <li>
          <svg viewBox="0 0 24 24" aria-hidden="true"><path d="M12 2a10 10 0 1 0 0 20 10 10 0 0 0 0-20zm-1 17.9A8 8 0 0 1 4.2 10.5L9 15.3v1a2 2 0 0 0 2 2zm6.9-2.5A2 2 0 0 0 16 16h-1v-3a1 1 0 0 0-1-1H8v-2h2a1 1 0 0 0 1-1V7h2a2 2 0 0 0 2-2v-.4a8 8 0 0 1 2.9 12.8z"/></svg>
          www.kestonfieldworks.com
        </li>
      </ul>
    </div>
  </section>

  <section class="card card-back" aria-label="Business card back">
    <div class="brand">
      <span class="brand-dot" aria-hidden="true"></span>
      <span class="brand-name">KESTON FIELDWORKS</span>
    </div>
    <div class="social-row">
      <span class="social-rule left"></span>
      <div class="social-links" aria-label="Social media links">
        <span class="social-link"></span>
        <span class="social-link"></span>
        <span class="social-link"></span>
      </div>
      <span class="social-rule right"></span>
    </div>
  </section>

</main>
</body>
</html>
```